Building company buisness cards

We are looking for a sharp modern new look for our business cards.
We are a New Zealand based company that specialises in house and land packages.
We have attached a photo of the current logo and would like to see if it can be improved somehow if needed.
We are open to any colours but we have chosen green at this stage.
Feel free to change the font and make the logo smarter looking.
Play with the colours and see what looks best.

We want a card that looks so good know one will want to throw it away!

Target Market(s)

Home buyers

Industry/Entity Type

Building

Contact Information for Business Card

Derek Tolvane
0217394062
dtolvane@quillmarkhomesteads.co.nz
quillmarkhomesteads.co.nz

Font styles to use
Serif
Sans Serif

Colors

Designer to choose colors to be used in the design.

Requirements
Must have
• Logo and company name on one side, details on the other side
Nice to have
• Color codes for the original green are HEX #4a8028, RGB(74,128,40), CMYK(42,0,69,50)
• Round corners, Raised and/or spot UV

```html
<!DOCTYPE html>
<html lang="en">
<head>
<meta charset="utf-8">
<title>Quillmark Homesteads — Business Card</title>
<link rel="stylesheet" href="https://fonts.googleapis.com/css2?family=Raleway:wght@400;500;700;800&display=swap">
<style>
  :root {
    --stage: #1b1c1e;
    --card-front: #ffffff;
    --card-back: #24282c;
    --brand-green: #3f8a2e;
    --ink: #2a2a2a;
    --rule: #b8b8b8;
    --copper: #c7733a;
    --copper-rule: #6b4a35;
  }
  * { margin: 0; padding: 0; box-sizing: border-box; }
  html, body {
    width: 800px;
    height: 1200px;
    overflow: hidden;
    background: var(--stage);
    font-family: "Raleway", sans-serif;
  }
  .canvas {
    width: 800px;
    height: 1200px;
    display: flex;
    flex-direction: column;
    align-items: center;
    justify-content: center;
    gap: 110px;
  }
  .card {
    width: 640px;
    height: 366px;
    border-radius: 26px;
    display: flex;
    flex-direction: column;
    align-items: center;
    justify-content: center;
    text-align: center;
  }
  .card--front {
    background: var(--card-front);
    border-bottom: 6px solid var(--brand-green);
  }
  .card--back { background: var(--card-back); }

  .wordmark {
    font-weight: 800;
    line-height: 0.98;
    letter-spacing: -0.5px;
  }
  .card--front .wordmark {
    color: var(--brand-green);
    font-size: 40px;
  }
  .card--back .wordmark {
    color: var(--copper);
    font-size: 58px;
  }
  .rule {
    height: 1px;
    background: var(--rule);
  }
  .card--front .rule--brand { width: 70px; margin: 14px 0 16px; }
  .card--front .rule--name { width: 130px; margin: 6px 0 10px; }
  .card--back .rule--brand {
    width: 90px;
    margin-top: 20px;
    background: var(--copper-rule);
  }
  .person-name {
    color: var(--brand-green);
    font-weight: 700;
    font-size: 22px;
  }
  .contact-list {
    list-style: none;
    font-size: 15px;
    color: var(--ink);
    line-height: 1.55;
    font-weight: 500;
  }
  .contact-list .label {
    color: var(--brand-green);
    font-weight: 700;
    margin-right: 4px;
  }
</style>
</head>
<body>
  <main class="canvas">
    <section class="card card--front" aria-label="Card front">
      <div class="wordmark">quillmark<br>homesteads.</div>
      <div class="rule rule--brand"></div>
      <div class="person-name">Derek Tolvane</div>
      <div class="rule rule--name"></div>
      <ul class="contact-list">
        <li><span class="label">P:</span>0217394062</li>
        <li><span class="label">E:</span>dtolvane@quillmarkhomesteads.co.nz</li>
        <li>quillmarkhomesteads.co.nz</li>
      </ul>
    </section>

    <section class="card card--back" aria-label="Card back">
      <div class="wordmark">quillmark<br>homesteads.</div>
      <div class="rule rule--brand"></div>
    </section>
  </main>
</body>
</html>
```